SkyvornQ Business Cards and Stationary Design

Need a design for our business cards and stationary. I want to carry on the theme of the logo. I want the business cards to have a design on the back. I would like the business cards and the stationary to carry the same theme, design scheme, and branding

Target Market(s)

Airlines and Maintenance Facilities

Industry/Entity Type

Aviation

Contact Information for Business Card

Name
Position Title
Address: 4827 Trellis Hollow Road, Fort Pierce, Florida, 34951
Office Number
Mobile Number
Email
Website

Font styles to use
Serif
Sans Serif

Colors

Designer to choose colors to be used in the design.

```html
<!DOCTYPE html>
<html lang="en">
<head>
<meta charset="utf-8">
<title>SkyvornQ Business Card</title>
<link href="https://fonts.googleapis.com/css2?family=Jost:wght@300;400;500;600&family=Open+Sans:wght@400;600&display=swap" rel="stylesheet">
<style>
  :root {
    --page-bg: #e9e7e4;
    --card-white: #ffffff;
    --brand-navy: #13305f;
    --brand-blue: #1b6dc1;
    --panel-blue: #0f5393;
    --accent-violet: #b44cf0;
    --text-white: #ffffff;
    --text-grey: #333b45;
  }
  * { margin: 0; padding: 0; box-sizing: border-box; }
  html, body { width: 1200px; height: 872px; overflow: hidden; }
  body {
    background: var(--page-bg);
    position: relative;
    font-family: "Open Sans", Arial, sans-serif;
  }
  .card {
    position: absolute;
    left: 250px;
    width: 700px;
    height: 400px;
    background: var(--card-white);
    box-shadow: 0 6px 18px rgba(0,0,0,0.12);
    overflow: hidden;
  }
  .card--front { top: 24px; }
  .card--back { top: 448px; }

  .brand {
    display: flex;
    align-items: center;
    gap: 14px;
  }
  .brand__dot {
    width: 40px; height: 40px;
    border-radius: 50%;
    background: var(--brand-blue);
    flex: none;
  }
  .brand__name {
    font-family: "Jost", sans-serif;
    font-weight: 600;
    color: var(--brand-navy);
    letter-spacing: 0.14em;
    text-transform: uppercase;
  }

  /* front */
  .front__content {
    position: absolute; inset: 0;
    display: flex; flex-direction: column;
    align-items: center; justify-content: center;
    gap: 22px;
  }
  .front__content .brand__name { font-size: 46px; }
  .front__content .brand__dot { width: 52px; height: 52px; }
  .front__url {
    font-family: "Open Sans", sans-serif;
    font-size: 17px;
    letter-spacing: 0.3em;
    color: var(--text-grey);
  }

  /* back */
  .back__brand-area {
    position: absolute; left: 0; top: 0;
    width: 330px; height: 400px;
    display: flex; align-items: center; justify-content: center;
  }
  .back__brand-area .brand { flex-direction: column; gap: 16px; }
  .back__brand-area .brand__name { font-size: 34px; }
  .back__brand-area .brand__dot { width: 64px; height: 64px; }

  .info-panel {
    position: absolute; left: 330px; top: 0;
    width: 370px; height: 400px;
    background: var(--panel-blue);
    border-left: 5px solid var(--accent-violet);
    color: var(--text-white);
    padding: 66px 20px 0 34px;
  }
  .info-panel__notch {
    position: absolute; left: -1px; top: 78px;
  }
  .person__name {
    font-family: "Jost", sans-serif;
    font-weight: 500;
    font-size: 27px;
    text-transform: uppercase;
    letter-spacing: 0.01em;
    line-height: 1.1;
  }
  .person__title {
    font-family: "Jost", sans-serif;
    font-weight: 300;
    font-size: 21px;
    text-transform: uppercase;
    margin-bottom: 26px;
  }
  .contact-list { list-style: none; }
  .contact-list li {
    display: flex; align-items: center; gap: 8px;
    font-size: 15.5px;
    line-height: 1.65;
  }
  .contact-list svg { width: 15px; height: 15px; flex: none; }
  .contact-list .address { align-items: flex-start; margin-top: 20px; line-height: 1.45; }
  .contact-list .address svg { margin-top: 3px; }
</style>
</head>
<body>

<section class="card card--front">
  <div class="front__content">
    <div class="brand">
      <span class="brand__dot"></span>
      <span class="brand__name">SkyvornQ</span>
    </div>
    <p class="front__url">www.skyvornq.com</p>
  </div>
</section>

<section class="card card--back">
  <div class="back__brand-area">
    <div class="brand">
      <span class="brand__dot"></span>
      <span class="brand__name">SkyvornQ</span>
    </div>
  </div>

  <div class="info-panel">
    <svg class="info-panel__notch" width="14" height="24" viewBox="0 0 14 24">
      <polygon points="0,0 12,12 0,24" fill="var(--card-white)" stroke="var(--accent-violet)" stroke-width="3"/>
    </svg>
    <h1 class="person__name">Dorian Velcourt</h1>
    <p class="person__title">President</p>
    <ul class="contact-list">
      <li>
        <svg viewBox="0 0 16 16" fill="none" stroke="currentColor" stroke-width="1.4"><circle cx="8" cy="8" r="7"/><path d="M5.5 4.5l1.2 1.8-.8.9a5 5 0 0 0 2.9 2.9l.9-.8 1.8 1.2-.8 1a6.5 6.5 0 0 1-6-6z"/></svg>
        772-555-0148
      </li>
      <li>
        <svg viewBox="0 0 16 16" fill="none" stroke="currentColor" stroke-width="1.4"><circle cx="8" cy="8" r="7"/><rect x="5.5" y="4" width="5" height="8" rx="1"/></svg>
        772-555-0193
      </li>
      <li>
        <svg viewBox="0 0 16 16" fill="none" stroke="currentColor" stroke-width="1.4"><circle cx="8" cy="8" r="7"/><rect x="4.2" y="5.5" width="7.6" height="5" /><path d="M4.2 5.5L8 8.5l3.8-3"/></svg>
        info@skyvornq.com
      </li>
      <li>
        <svg viewBox="0 0 16 16" fill="none" stroke="currentColor" stroke-width="1.3"><circle cx="8" cy="8" r="7"/><ellipse cx="8" cy="8" rx="3" ry="7"/><path d="M1 8h14M2 4.5h12M2 11.5h12"/></svg>
        www.skyvornq.com
      </li>
      <li class="address">
        <svg viewBox="0 0 16 16" fill="none" stroke="currentColor" stroke-width="1.4"><circle cx="8" cy="8" r="7"/><path d="M8 12.5s-3-3-3-5.2a3 3 0 0 1 6 0c0 2.2-3 5.2-3 5.2z"/><circle cx="8" cy="7.2" r="1"/></svg>
        <span>4827 Trellis Hollow Road,<br>Fort Pierce, Florida, 34951</span>
      </li>
    </ul>
  </div>
</section>

</body>
</html>
```